Postcard design to acquire new clients for my Property Management Company

I'm looking for a postcard design that I can send to prospective clients detailing information about my company and services.
Postcard should be eye catching and contain information from www.bramblecrestpm.com. I've provided a few screen shots for the most important information and my logo.
Target Market(s)
Real Estate
Industry/Entity Type
Real Estate
Font styles to use
Sans Serif
Requirements
Must have
- Must be eye catching!! this will be a direct mail piece - I'd like for the card to be read and not tossed in the trash immediately.
Design que from the logo.
A place to write / print the receipts name and address.
our physical address - 2387 Hollow Pine Road, Lubbock, TX 79852.
Should not have
- the contact information on the business card is not accurate - please use info from website.

```html
<!DOCTYPE html>
<html lang="en">
<head>
<meta charset="utf-8">
<title>Bramblecrest Property Management Postcard</title>
<link rel="stylesheet" href="https://fonts.googleapis.com/css2?family=Montserrat:wght@600;800&family=Roboto+Condensed:wght@300;400;700;800&display=swap">
<style>
  :root {
    --navy: #172a55;
    --blue: #1b5aa6;
    --blue-light: #2f7ccc;
    --yellow: #f6c400;
    --ink: #111418;
    --white: #ffffff;
    --sky: #b9d6ee;
  }
  * { margin: 0; padding: 0; box-sizing: border-box; }
  html, body { width: 1200px; height: 850px; overflow: hidden; background: var(--white); }
  .postcard {
    position: relative;
    width: 1200px;
    height: 850px;
    overflow: hidden;
    background: var(--white);
    font-family: "Roboto Condensed", "Arial Narrow", sans-serif;
  }
  .shapes { position: absolute; inset: 0; }

  .photo-main {
    position: absolute; inset: 0;
    clip-path: polygon(660px 0, 1200px 0, 1200px 560px, 900px 640px, 700px 380px);
    background: linear-gradient(160deg, #cfe4f5 0%, #e8e4dc 40%, #c9a98f 62%, #5fb6d8 85%, #3d8fb8 100%);
  }
  .photo-side {
    position: absolute; inset: 0;
    clip-path: polygon(1200px 430px, 1200px 780px, 930px 780px, 985px 600px);
    background: linear-gradient(170deg, #d8e9f6 0%, #f3f1ec 45%, #d9d3c8 70%, #8fb7cf 100%);
  }

  .brand {
    position: absolute; left: 40px; top: 52px;
    color: var(--navy);
    font-family: "Montserrat", Arial, sans-serif;
  }
  .brand-name {
    font-size: 62px; font-weight: 800; letter-spacing: 3px; line-height: 1;
  }
  .brand-sub {
    margin-top: 8px; font-size: 25px; font-weight: 600; letter-spacing: 6.5px; line-height: 1;
  }

  .headline {
    position: absolute; left: 44px; top: 188px;
    color: var(--white);
    font-weight: 800; text-transform: uppercase; line-height: 1.02;
  }
  .headline span { display: block; font-size: 40px; }
  .headline .accent { color: var(--yellow); }
  .headline .accent-lg { color: var(--yellow); font-size: 48px; letter-spacing: 0.5px; }

  .services {
    position: absolute; left: 44px; top: 408px;
    list-style: none;
    color: var(--ink);
    font-weight: 700; font-size: 29px; line-height: 37.5px; letter-spacing: 0.3px;
  }

  .tagline {
    position: absolute; left: 44px; top: 722px;
    color: var(--navy);
    font-weight: 800; font-size: 22px; line-height: 24px; text-transform: uppercase;
  }

  .offer {
    position: absolute; left: 790px; top: 480px;
    width: 188px; height: 188px; border-radius: 50%;
    background: var(--yellow);
    border: 6px solid var(--blue);
    display: flex; flex-direction: column; align-items: center; justify-content: center;
    color: var(--navy); text-align: center; line-height: 1.02;
  }
  .offer .small { font-size: 26px; font-weight: 700; }
  .offer .big { font-size: 46px; font-weight: 800; }

  .contact-bar {
    position: absolute; left: 0; bottom: 0; width: 1200px; height: 68px;
    background: var(--navy);
    color: var(--white);
    display: flex; align-items: center; justify-content: center;
    font-weight: 300; font-size: 50px; letter-spacing: 1px; white-space: nowrap;
  }
</style>
</head>
<body>
<main class="postcard">
  <div class="photo-main" role="img" aria-label="Photo of a modern luxury house with a swimming pool"></div>
  <div class="photo-side" role="img" aria-label="Photo of a white modern apartment building"></div>

  <svg class="shapes" width="1200" height="850" viewBox="0 0 1200 850" aria-hidden="true">
    <defs>
      <linearGradient id="bannerBlue" x1="0" y1="0" x2="1" y2="1">
        <stop offset="0" stop-color="#1b5aa6"/>
        <stop offset="1" stop-color="#134a8c"/>
      </linearGradient>
    </defs>
    <!-- top accent -->
    <polygon points="540,0 930,0 700,240" fill="var(--yellow)"/>
    <polygon points="640,0 668,0 720,390 700,392" fill="var(--blue)"/>
    <!-- side photo frame -->
    <polygon points="1200,380 1200,430 985,600 930,780 880,780 955,575" fill="var(--blue)"/>
    <!-- headline banner -->
    <polygon points="0,168 740,168 690,372 0,372" fill="url(#bannerBlue)"/>
    <polygon points="0,372 690,372 685,386 0,386" fill="var(--yellow)"/>
    <!-- tagline ribbon -->
    <polygon points="0,716 490,716 460,782 0,782" fill="var(--yellow)"/>
  </svg>

  <header class="brand">
    <div class="brand-name">BRAMBLECREST</div>
    <div class="brand-sub">PROPERTY MANAGEMENT</div>
  </header>

  <h1 class="headline">
    <span>Maximize your</span>
    <span class="accent">Financial returns</span>
    <span>With support from our</span>
    <span class="accent-lg">Rental specialists</span>
  </h1>

  <ul class="services">
    <li>PROPERTY MARKETING</li>
    <li>TENANT SCREENING</li>
    <li>RENT COLLECTION</li>
    <li>MAINTENANCE</li>
    <li>PROPERTY INSPECTIONS</li>
    <li>FINANCIAL REPORTING</li>
    <li>EVICTIONS</li>
    <li>LEGAL GUIDANCE</li>
  </ul>

  <p class="tagline">Choose the right<br>property management system</p>

  <div class="offer">
    <span class="small">Get A</span>
    <span class="big">FREE</span>
    <span class="small">Rental</span>
    <span class="small">Analysis</span>
  </div>

  <footer class="contact-bar">806-555-0142 | www.bramblecrestpm.com</footer>
</main>
</body>
</html>
```